Accounting firm needing business card / letterhead designed
Marcus L. Trenholm, CPA
marcus@veltrowledger.com
www.veltrowledger.com
842 E Alder Ave Larkmoor, WV 43827
419-562-0974

```html
<!DOCTYPE html>
<html lang="en">
<head>
<meta charset="utf-8">
<title>Veltrow Ledger – Business Card</title>
<link href="https://fonts.googleapis.com/css2?family=Roboto:wght@400;500&family=Roboto+Condensed:wght@700&display=swap" rel="stylesheet">
<style>
  :root {
    --navy: #23205c;
    --green: #7fbf3b;
    --paper: #f4f4f4;
    --ink: #4a4a4a;
    --backdrop: #e6e3df;
    --white: #ffffff;
  }
  * { margin: 0; padding: 0; box-sizing: border-box; }
  html, body { width: 1200px; height: 960px; overflow: hidden; }
  body {
    background: var(--backdrop);
    position: relative;
    font-family: "Roboto", Arial, sans-serif;
  }
  .card {
    position: absolute;
    width: 600px;
    height: 343px;
    box-shadow: 0 3px 8px rgba(0,0,0,0.25);
  }
  .card-front { left: 314px; top: 113px; background: var(--paper); }
  .card-back { left: 311px; top: 472px; background: var(--navy); }

  .brand-name {
    font-family: "Roboto", Arial, sans-serif;
    font-weight: 500;
    letter-spacing: 3px;
    text-transform: uppercase;
    white-space: nowrap;
  }
  .card-front .brand-name {
    position: absolute;
    right: 44px;
    top: 60px;
    font-size: 34px;
    color: var(--navy);
  }
  .card-back .brand-name {
    position: absolute;
    left: 0; right: 0;
    top: 118px;
    text-align: center;
    font-size: 44px;
    color: var(--white);
  }

  .accent-bar {
    position: absolute;
    left: 0; top: 203px;
    width: 12px; height: 32px;
    background: var(--green);
  }
  .holder-name {
    position: absolute;
    left: 42px; top: 205px;
    font-family: "Roboto Condensed", "Arial Narrow", sans-serif;
    font-weight: 700;
    font-size: 22px;
    color: var(--navy);
  }
  .contact-list {
    position: absolute;
    left: 43px; top: 249px;
    list-style: none;
    font-size: 14.5px;
    line-height: 19px;
    color: var(--ink);
  }
  .contact-list li { display: flex; align-items: center; gap: 8px; }
  .contact-list svg { width: 13px; height: 13px; fill: var(--navy); flex: none; }
  .contact-divider {
    position: absolute;
    left: 253px; top: 270px;
    width: 1px; height: 36px;
    background: #9a9a9a;
  }
  .address {
    position: absolute;
    left: 277px; top: 268px;
    font-size: 14.5px;
    line-height: 19px;
    color: var(--ink);
    font-style: normal;
  }

  .web-band {
    position: absolute;
    left: 0; top: 278px;
    width: 100%; height: 37px;
    background: var(--green);
    display: flex; align-items: center; justify-content: center;
    color: var(--white);
    font-size: 14px;
    letter-spacing: 6px;
  }
  .web-band strong { font-weight: 500; }
</style>
</head>
<body>
  <section class="card card-front">
    <div class="brand-name">Veltrow Ledger</div>
    <div class="accent-bar"></div>
    <h1 class="holder-name">Marcus L. Trenholm, CPA</h1>
    <ul class="contact-list">
      <li>
        <svg viewBox="0 0 24 24"><path d="M6.6 10.8a15.1 15.1 0 0 0 6.6 6.6l2.2-2.2c.3-.3.7-.4 1-.2 1.1.4 2.3.6 3.6.6.6 0 1 .4 1 1V20c0 .6-.4 1-1 1C10.6 21 3 13.4 3 4c0-.6.4-1 1-1h3.5c.6 0 1 .4 1 1 0 1.2.2 2.4.6 3.6.1.3 0 .7-.2 1z"/></svg>
        538-562-0974
      </li>
      <li>
        <svg viewBox="0 0 24 24"><path d="M2 5h20v14H2z M4 7v.5l8 5 8-5V7l-8 5z" fill-rule="evenodd"/></svg>
        marcus@veltrowledger.com
      </li>
      <li>
        <svg viewBox="0 0 24 24"><path d="M12 2a10 10 0 1 0 0 20 10 10 0 0 0 0-20zm-1 17.9A8 8 0 0 1 4.2 10.2L9 15v1a2 2 0 0 0 2 2zm6.9-2.5A2 2 0 0 0 16 16h-1v-3a1 1 0 0 0-1-1H8v-2h2a1 1 0 0 0 1-1V7h2a2 2 0 0 0 2-2v-.4a8 8 0 0 1 2.9 12.8z"/></svg>
        www.veltrowledger.com
      </li>
    </ul>
    <div class="contact-divider"></div>
    <address class="address">842 E Alder Ave<br>Larkmoor, WV 43827</address>
  </section>

  <section class="card card-back">
    <div class="brand-name">Veltrow Ledger</div>
    <div class="web-band">www.<strong>veltrowledger</strong>.com</div>
  </section>
</body>
</html>
```